Vantrel Intergrated Marketing Stationary Design Contest

We require a very professional looking stationary set to include: letterhead, compliments slip and business cards (double sided bus cards).

Files should be supplied on either Illustrator or InDesign.

We are interested in perhaps encorporating a faint watermark with the letter q or the logo, but it isnt a pre-requisite

Target Market(s)

Business owners seeking professional marketing services

Industry/Entity Type

Marketing

Requirements
Must have
• Concurrent theme wiht business cards, letterhead and comp slip. Must be an editable document for future ammendment
Should not have
• No use of times new roman or similar fonts

```html
<!DOCTYPE html>
<html lang="en">
<head>
<meta charset="utf-8">
<title>Vantrel Intergrated Marketing – Letterhead</title>
<link rel="stylesheet" href="https://fonts.googleapis.com/css2?family=Jost:wght@300;400&display=swap">
<style>
  :root {
    --brand-orange: #f15a2b;
    --ink: #1f1f1f;
    --paper: #ffffff;
  }
  html, body {
    margin: 0;
    padding: 0;
    overflow: hidden;
    background: var(--paper);
  }
  .letterhead {
    position: relative;
    width: 848px;
    height: 1200px;
    background: var(--paper);
    font-family: "Jost", sans-serif;
    font-weight: 300;
    color: var(--ink);
    overflow: hidden;
  }
  .brand-mark {
    position: absolute;
    top: 60px;
    right: 30px;
    display: flex;
    align-items: center;
    gap: 10px;
  }
  .brand-name {
    font-size: 22px;
    font-weight: 400;
    color: var(--brand-orange);
    letter-spacing: 0.5px;
  }
  .brand-dot {
    display: block;
    width: 44px;
    height: 44px;
  }
  .contact-list {
    position: absolute;
    left: 41px;
    top: 1002px;
    margin: 0;
    font-size: 14px;
    line-height: 16px;
  }
  .contact-row {
    display: flex;
  }
  .contact-label {
    width: 20px;
    color: var(--brand-orange);
  }
  .contact-row dd {
    margin: 0;
  }
  .company-address {
    position: absolute;
    left: 41px;
    top: 1078px;
    margin: 0;
    font-style: normal;
    font-size: 14px;
    line-height: 16px;
  }
  .company-name {
    color: var(--brand-orange);
  }
  .legal-details {
    position: absolute;
    left: 41px;
    top: 1139px;
    margin: 0;
    font-size: 11px;
    line-height: 12.6px;
  }
  .legal-label {
    color: var(--brand-orange);
  }
</style>
</head>
<body>
<main class="letterhead">
  <header class="brand-mark">
    <span class="brand-name">Vantrel</span>
    <svg class="brand-dot" viewBox="0 0 44 44" aria-hidden="true">
      <circle cx="22" cy="22" r="22" fill="var(--brand-orange)"/>
    </svg>
  </header>

  <footer>
    <dl class="contact-list">
      <div class="contact-row"><dt class="contact-label">T</dt><dd>01632 960514</dd></div>
      <div class="contact-row"><dt class="contact-label">F</dt><dd>01632 960517</dd></div>
      <div class="contact-row"><dt class="contact-label">E</dt><dd>enquiries@vantrelim.co.uk</dd></div>
      <div class="contact-row"><dt class="contact-label">W</dt><dd>www.vantrelim.co.uk</dd></div>
    </dl>

    <address class="company-address">
      <span class="company-name">Vantrel Intergrated Marketing</span><br>
      Halden House, Mercer Street,<br>
      Brackmoor, West Yorkshire, WF9 4RX
    </address>

    <p class="legal-details">
      <span class="legal-label">Company Registration</span> 4817305<br>
      <span class="legal-label">Vat No</span> 582 4719 06<br>
      Trading as a division of Brennoc Ltd
    </p>
  </footer>
</main>
</body>
</html>
```